Venture Capital firm needs modern business cards

We are a Venture Capital firm within financial services/Asset management. The industry generally has basic business cards with black, blue and maybe green/yellow design elements.
Our firm has a four-colour swoosh logo. We are based in London and want to stand out, just a little bit!, from the crowd. Our company is called LORV Investments and the 'C' stands for collaboration thus using makerswarm is a natural portal for our business card design competition. Our logo came via makerswarm too!
We use 'Venture Partner in Asset Management' as our tagline and this is Trademark registered. We operate in a conservative industry and we should not overstep our mark. The logo is colorful as it is and therefore the rest of the design should not be too fanciful.
The objective is twofold: make our logo element stick and memorable with our audience, whilst representing a conservative yet young image.
Updates
The Business Card obviously needs a field for Name, Surname, Job Title, Adress fields: Street, City, Postcode, Country, telefone and cell number, website address, etc.
We have uploaded the ai file. We trust that these are OK. If not, please advise.
Reason: We have have been busy with a client engagement. We will set the project as Guaranteed in return for the troubles we cause. Apologies for the confusion.
Thank you all for these great and creative design suggestions. The team is very happy with a number of your ideas! We will be in touch tomorrow to give individual feedback before the project closes on Friday. We look forward to working with some of you to narrow down your creations. Thank you, LORV Investments team.
All,
Target Market(s)
Financial Services Professionals, Investors, Media, 35-70 years, mainly male, well educated
Industry/Entity Type
Conservative
Requirements
Must have
- We must make use of our logo and potential tagline 'Venture Partner in Asset Management' as we are establishing a new Brand and new company in the market.
We can use 'LORV', 'LORV Investments', and 'LORV Investments'+tagline 'Venture Partner in Asset Management' or simply the four-colour swoosh plus the name of the company as part of the text. (see files)
All design elements are available in black or grey-scale if required. (grey scale swoosh attached).
Due to regulation we must have the following wording on the card in small print 'LORV Investments is an Appointed Representative of Bramwell Holdings Partnership Limited, which is authorised by the Monetary Oversight Board'.
Nice to have
- We would consider designs that make use of different printing techniques such embossing/debossing, UV spot etc.
We attach our colour palette in the files section for your reference.
Should not have
- The font we use for our company name is 'EXO' so do not use a font style that clashes with the corporate fonts, please.
Do not use other design elements than the ones we provide in the file library as part of this project.

```html
<!DOCTYPE html>
<html lang="en">
<head>
<meta charset="utf-8">
<title>LORV Investments — Business Card</title>
<link rel="stylesheet" href="https://fonts.googleapis.com/css2?family=Exo+2:wght@400;600;700&family=Barlow:wght@400;600;700&display=swap">
<style>
  :root {
    --stage: #d6d6d6;
    --card: #fbfbfa;
    --ink-dark: #3a3b3d;
    --ink-grey: #8a8b8d;
    --ink-light: #9d9ea0;
    --accent-green: #8dc63f;
    --swoosh-green: #3fa535;
    --swoosh-teal: #2ab3c9;
    --swoosh-orange: #f7a823;
    --swoosh-pink: #e2336f;
  }
  * { box-sizing: border-box; margin: 0; padding: 0; }
  html, body { width: 1200px; height: 800px; overflow: hidden; }
  body {
    background: var(--stage);
    font-family: "Barlow", Arial, sans-serif;
    display: flex;
    align-items: center;
    justify-content: center;
    gap: 40px;
  }
  .card {
    width: 540px;
    height: 310px;
    background: var(--card);
    position: relative;
    overflow: hidden;
    box-shadow: 0 6px 18px rgba(0,0,0,0.18);
  }

  /* Back of card */
  .card-back__swoosh-field {
    position: absolute;
    inset: 0;
    background:
      radial-gradient(ellipse 60% 45% at 8% 100%, rgba(63,165,53,0.55), transparent 70%),
      radial-gradient(ellipse 55% 40% at 95% 0%, rgba(42,179,201,0.5), transparent 70%),
      radial-gradient(ellipse 22% 35% at 22% 0%, rgba(247,168,35,0.55), transparent 70%),
      radial-gradient(ellipse 18% 35% at 90% 75%, rgba(226,51,111,0.45), transparent 70%);
  }
  .tagline {
    position: absolute;
    left: 200px;
    top: 62px;
    font-family: "Exo 2", Arial, sans-serif;
    color: var(--ink-light);
    line-height: 0.92;
  }
  .tagline__small { font-size: 26px; display: block; }
  .tagline__large { font-size: 44px; display: block; font-weight: 600; }
  .tagline__tiny { font-size: 20px; display: block; }
  .tagline__url {
    display: block;
    margin-top: 8px;
    font-family: "Barlow", Arial, sans-serif;
    font-size: 13px;
    letter-spacing: 0.5px;
  }
  .tagline__url strong { color: var(--accent-green); font-weight: 700; }

  /* Front of card */
  .brand {
    position: absolute;
    left: 100px;
    top: 70px;
    display: flex;
    align-items: center;
    gap: 14px;
  }
  .brand__dot {
    width: 38px;
    height: 38px;
    border-radius: 50%;
    background: var(--accent-green);
  }
  .brand__name {
    font-family: "Exo 2", Arial, sans-serif;
    font-weight: 600;
    font-size: 42px;
    color: var(--ink-dark);
    letter-spacing: 0.5px;
  }
  .contact {
    position: absolute;
    left: 318px;
    top: 150px;
    list-style: none;
    font-size: 14px;
    color: var(--ink-grey);
    line-height: 1.1;
  }
  .contact__item {
    display: flex;
    align-items: flex-start;
    gap: 8px;
    margin-bottom: 3px;
  }
  .contact__icon { width: 13px; height: 13px; flex: none; margin-top: 1px; fill: var(--accent-green); }
  .cardholder {
    position: absolute;
    left: 36px;
    top: 226px;
  }
  .cardholder__name {
    font-weight: 700;
    font-size: 19px;
    color: var(--ink-grey);
    letter-spacing: 0.5px;
  }
  .cardholder__role {
    font-size: 16px;
    color: var(--accent-green);
    margin-top: 2px;
  }
</style>
</head>
<body>

  <section class="card card-back" aria-label="Card back">
    <div class="card-back__swoosh-field" role="img" aria-label="Enlarged four-colour swoosh decoration in green, teal, orange and pink"></div>
    <p class="tagline">
      <span class="tagline__small">Venture</span>
      <span class="tagline__large">Partner</span>
      <span class="tagline__tiny">in</span>
      <span class="tagline__large">Asset</span>
      <span class="tagline__small">Management</span>
      <span class="tagline__url">www.<strong>lorvinvestments</strong>.com</span>
    </p>
  </section>

  <section class="card card-front" aria-label="Card front">
    <div class="brand">
      <span class="brand__dot"></span>
      <span class="brand__name">LORV Investments</span>
    </div>

    <ul class="contact">
      <li class="contact__item">
        <svg class="contact__icon" viewBox="0 0 12 12"><path d="M6 0a4 4 0 0 0-4 4c0 3 4 8 4 8s4-5 4-8a4 4 0 0 0-4-4zm0 5.6A1.6 1.6 0 1 1 6 2.4a1.6 1.6 0 0 1 0 3.2z"/></svg>
        <span>01 01 Avenue, Suite No. 123,<br>Your City, Country</span>
      </li>
      <li class="contact__item">
        <svg class="contact__icon" viewBox="0 0 12 12"><circle cx="6" cy="6" r="6"/><path d="M4 3l1 1.5-.7.8a4 4 0 0 0 2.4 2.4l.8-.7L9 8l-.6 1A5 5 0 0 1 3 3.6z" fill="#fbfbfa"/></svg>
        <span>+012 345 6789</span>
      </li>
      <li class="contact__item">
        <svg class="contact__icon" viewBox="0 0 12 12"><rect x="3" y="0" width="6" height="4"/><rect x="0" y="5" width="12" height="7" rx="1"/></svg>
        <span>+012 345 6780</span>
      </li>
      <li class="contact__item">
        <svg class="contact__icon" viewBox="0 0 12 12"><rect x="0" y="2" width="12" height="8" rx="1"/><path d="M1 3l5 4 5-4" stroke="#fbfbfa" fill="none"/></svg>
        <span>name@lorvinvestments.com</span>
      </li>
      <li class="contact__item">
        <svg class="contact__icon" viewBox="0 0 12 12"><circle cx="6" cy="6" r="6"/><path d="M0 6h12M6 0c-3 3-3 9 0 12M6 0c3 3 3 9 0 12" stroke="#fbfbfa" fill="none" stroke-width="0.8"/></svg>
        <span>www.lorvinvestments.com</span>
      </li>
    </ul>

    <div class="cardholder">
      <p class="cardholder__name">CARDHOLDER NAME</p>
      <p class="cardholder__role">Designation</p>
    </div>
  </section>

</body>
</html>
```